Ellismere Air Business Card Design

Design new, 2 sides, business cards for a residential and light commercial heating, air conditioning contractor.

Target Market(s)

Homeowners, small businesses

Industry/Entity Type

Business

Contact Information for Business Card

Dominic Westerhall
Phone - 862-415-2736
Email
Address - PO box 518
Brightwater NJ 07912
Website - www.EllismereAirLLC.example

Requirements
Must have
• logo, company colors, standard size with no die cut, so I can use nova stamp

```html
<!DOCTYPE html>
<html lang="en">
<head>
<meta charset="utf-8">
<title>Ellismere Air Business Card</title>
<link rel="stylesheet" href="https://fonts.googleapis.com/css2?family=Lato:wght@400;700&display=swap">
<style>
  :root {
    --brand-red: #9b2233;
    --brand-orange: #f39a1e;
    --text-grey: #7a7a7a;
    --card-white: #ffffff;
    --backdrop: #ece8e3;
  }
  * { box-sizing: border-box; margin: 0; padding: 0; }
  html, body { width: 1200px; height: 880px; overflow: hidden; }
  body {
    background: var(--backdrop);
    font-family: "Lato", sans-serif;
    position: relative;
  }
  .card {
    position: absolute;
    left: 320px;
    width: 560px;
    height: 320px;
    overflow: hidden;
    box-shadow: 0 6px 18px rgba(0,0,0,0.18);
  }
  /* Back side */
  .card--back { top: 60px; background: var(--brand-red); }
  .card--back .brand-name {
    position: absolute;
    left: 0; width: 500px; top: 118px;
    text-align: center;
    font-size: 34px; font-weight: 700;
    color: var(--brand-orange);
    white-space: nowrap;
  }
  .card--back .rule {
    position: absolute;
    left: 20px; top: 262px;
    width: 270px; height: 2px;
    background: var(--card-white);
  }
  .card--back .web {
    position: absolute;
    left: 302px; top: 251px;
    font-size: 17px; color: var(--card-white);
    white-space: nowrap;
  }
  /* Front side */
  .card--front { top: 500px; background: var(--card-white); }
  .card--front .brand-name {
    position: absolute;
    left: 250px; width: 280px; top: 62px;
    text-align: center;
    font-size: 32px; font-weight: 700;
    color: var(--brand-red);
    white-space: nowrap;
  }
  .card--front .band {
    position: absolute;
    left: 0; right: 0; bottom: 0; height: 68px;
    background: var(--brand-red);
  }
  .card--front .band-line {
    position: absolute;
    left: 0; right: 0; bottom: 80px; height: 2px;
    background: var(--brand-orange);
  }
  .identity {
    position: absolute;
    left: 22px; top: 140px; width: 236px;
    text-align: right;
  }
  .identity .person {
    font-size: 21px; font-weight: 700;
    color: var(--brand-orange);
    margin-bottom: 6px;
    white-space: nowrap;
  }
  .identity .address {
    font-size: 15px; line-height: 1.3;
    color: var(--text-grey);
  }
  .divider {
    position: absolute;
    left: 272px; top: 172px;
    width: 2px; height: 58px;
    background: var(--text-grey);
  }
  .contacts {
    position: absolute;
    left: 286px; top: 168px;
    list-style: none;
  }
  .contacts li {
    display: flex; align-items: center; gap: 7px;
    font-size: 14px; line-height: 22px;
    color: var(--text-grey);
    white-space: nowrap;
  }
  .contacts svg { width: 12px; height: 12px; flex: none; }
</style>
</head>
<body>

<section class="card card--back" aria-label="Card back">
  <div class="brand-name">Ellismere Air</div>
  <div class="rule"></div>
  <div class="web">www.EllismereAirLLC.example</div>
</section>

<section class="card card--front" aria-label="Card front">
  <div class="brand-name">Ellismere Air</div>

  <div class="identity">
    <div class="person">Dominic Westerhall</div>
    <div class="address">PO box 518<br>Brightwater NJ 07912</div>
  </div>

  <div class="divider"></div>

  <ul class="contacts">
    <li>
      <svg viewBox="0 0 12 12" aria-hidden="true"><path d="M2.5 1 L4.5 1 L5.2 3.6 L3.9 4.6 Q5 7 7.4 8.1 L8.4 6.8 L11 7.5 L11 9.5 Q10.5 11 8.8 11 Q1 10.3 1 2.8 Q1 1.5 2.5 1 Z" fill="var(--brand-orange)"/></svg>
      862-415-2736
    </li>
    <li>
      <svg viewBox="0 0 12 12" aria-hidden="true"><rect x="0.5" y="2.5" width="11" height="7" fill="var(--brand-orange)"/><path d="M0.5 2.5 L6 6.5 L11.5 2.5" fill="none" stroke="#fff" stroke-width="1"/></svg>
      info@EllismereAirLLC.example
    </li>
    <li>
      <svg viewBox="0 0 12 12" aria-hidden="true"><g fill="none" stroke="var(--brand-orange)" stroke-width="1"><circle cx="6" cy="6" r="5"/><ellipse cx="6" cy="6" rx="2.2" ry="5"/><path d="M1 6 H11 M2 3.5 H10 M2 8.5 H10"/></g></svg>
      www.EllismereAirLLC.example
    </li>
  </ul>

  <div class="band-line"></div>
  <div class="band"></div>
</section>

</body>
</html>
```